Diverse, up-scale salon needs eye-catching, unique business cards.

We are looking for a unique business card design for our stylist but that can also be multi functional and used for appointment reminder and referrals. I will need a design in a format that I can modify names and titles going forward. In the past we have had a dark background with the logo on one side, and stylist and contact information on the other but we are open to all ideas. I have included our mission statement as well as branded colors below. The statement doesn't need to go on the card, it's just a reference for target market. We need space for the stylists name, title, instagram handle and then the salons phone number, website and address. I am also open to adding a spot for a qr code linked to the stylist instagram or the salon booking link.

primary brand colors:
#333333 #233415 #36502a #93874a #000000
Mission statement:
Vessolin Hair Studio, a high-end salon located in the lively Downtown Farmington, Michigan, is committed to providing exceptional services in a welcoming and relaxed environment to meet the needs of our diverse clientele.
Our salon specializes in contemporary custom haircuts, coloring, extensions, and barbering and beard grooming services. Our team of skilled stylists is passionate and inventive in their hair styling techniques. At the heart of our salon are values centered on quality, innovation, creativity, and above all, comfort. These core values are evident in every appointment across our customizable array of services.
Our goal is to establish a benchmark for exceptional hair care for every human.
Website: www.vessolinhairstudio.example
instagram: @vessolinhairstudio
address: 41782 Pelham Crest Rd, Harwick Falls OR
phone: 555-613-4087

Industry/Entity Type

Hair Salon

Contact Information for Business Card

Stylist name, title, phone, instagram, website, address, (optional qr code)

Requirements
Should not have
• Does not need mission statement on the card.

```html
<!DOCTYPE html>
<html lang="en">
<head>
<meta charset="utf-8">
<title>Vessolin Hair Studio – Business Card</title>
<link href="https://fonts.googleapis.com/css2?family=Poppins:wght@400;600;800&display=swap" rel="stylesheet">
<style>
  :root {
    --stage: #d6d6d6;
    --gold: #8f8549;
    --gold-dark: #877c43;
    --gold-light: #969050;
    --paper: #f7f7f8;
    --paper-shade: #ececee;
    --ink: #111111;
    --pill: #232323;
    --white: #ffffff;
  }
  * { box-sizing: border-box; margin: 0; padding: 0; }
  html, body { width: 937px; height: 1200px; overflow: hidden; }
  body {
    background: var(--stage);
    font-family: "Poppins", sans-serif;
    position: relative;
  }
  .card {
    position: absolute;
    left: 93px;
    width: 751px;
    height: 428px;
    overflow: hidden;
    box-shadow: 6px 10px 14px rgba(0,0,0,0.28);
  }
  .card-front { top: 131px; }
  .card-back { top: 642px; }

  .texture { position: absolute; inset: 0; }
  .card-front .texture {
    background: linear-gradient(135deg, var(--gold-dark), var(--gold-light) 50%, var(--gold-dark));
  }
  .card-back .texture {
    background: linear-gradient(135deg, var(--paper-shade), var(--paper) 45%, var(--white));
  }

  .brand-mark {
    position: absolute;
    border-radius: 50%;
    display: flex;
    align-items: center;
    justify-content: center;
    text-align: center;
    font-weight: 600;
    line-height: 1.25;
  }
  .card-front .brand-mark {
    left: 270px; top: 105px;
    width: 210px; height: 210px;
    border: 3px solid var(--white);
    color: var(--white);
    font-size: 22px;
  }
  .card-back .brand-mark {
    left: 104px; top: 107px;
    width: 174px; height: 174px;
    border: 3px solid var(--gold);
    color: var(--gold);
    font-size: 19px;
  }

  .stylist {
    position: absolute;
    left: 360px; top: 80px;
    width: 320px;
  }
  .stylist-name {
    font-size: 31px;
    font-weight: 800;
    color: var(--ink);
    letter-spacing: 0.01em;
    line-height: 1.2;
  }
  .stylist-studio {
    font-size: 18px;
    font-weight: 400;
    color: var(--gold);
    line-height: 1.3;
    margin-top: 2px;
  }
  .divider {
    position: relative;
    width: 298px;
    height: 3px;
    margin-top: 15px;
  }
  .divider::before {
    content: ""; position: absolute; left: 0; right: 0; top: 1px;
    height: 1px; background: var(--gold);
  }
  .divider::after {
    content: ""; position: absolute; left: 0; top: 0;
    width: 52px; height: 3px; background: var(--gold);
  }

  .contact-list {
    list-style: none;
    margin-top: 21px;
  }
  .contact-list li {
    display: flex;
    align-items: flex-start;
    font-size: 17px;
    color: var(--ink);
    line-height: 24px;
    margin-bottom: 12px;
  }
  .contact-list svg {
    flex: 0 0 auto;
    width: 17px; height: 17px;
    margin: 4px 12px 0 2px;
  }

  .footer-band {
    position: absolute;
    left: 0; right: 0; bottom: 0;
    height: 64px;
    background: var(--gold);
  }
  .web-pill {
    position: absolute;
    left: 90px; top: 345px;
    width: 571px; height: 42px;
    background: var(--pill);
    border: 2px solid var(--white);
    border-radius: 21px;
    display: flex; align-items: center; justify-content: center;
    color: var(--white);
    font-size: 18px;
    letter-spacing: 0.28em;
    font-weight: 400;
  }
  .web-pill strong { font-weight: 600; }
</style>
</head>
<body>

  <section class="card card-front">
    <div class="texture" role="img" aria-label="Soft diamond pattern in olive gold tones"></div>
    <div class="brand-mark">Vessolin<br>Hair Studio</div>
  </section>

  <section class="card card-back">
    <div class="texture" role="img" aria-label="Soft diamond pattern in light grey tones"></div>
    <div class="footer-band"></div>

    <div class="brand-mark">Vessolin<br>Hair Studio</div>

    <div class="stylist">
      <h1 class="stylist-name">DANIEL REYES</h1>
      <p class="stylist-studio">Vessolin Hair Studio</p>
      <div class="divider"></div>

      <ul class="contact-list">
        <li>
          <svg viewBox="0 0 20 20" aria-hidden="true">
            <circle cx="10" cy="10" r="9.5" fill="var(--gold)"/>
            <path d="M7 5.5l1.6 2.4-1 1c.6 1.3 1.6 2.3 2.9 2.9l1-1 2.4 1.6-.8 1.6c-3.6-.3-6.6-3.3-6.9-6.9z" fill="var(--white)"/>
          </svg>
          <span>555-613-4087</span>
        </li>
        <li>
          <svg viewBox="0 0 20 20" aria-hidden="true">
            <path d="M10 1.5a6 6 0 0 0-6 6c0 4.3 6 10 6 10s6-5.7 6-10a6 6 0 0 0-6-6z" fill="var(--gold)"/>
            <circle cx="10" cy="7.5" r="2.3" fill="var(--white)"/>
          </svg>
          <span>41782 Pelham Crest Rd,<br>Harwick Falls OR</span>
        </li>
        <li>
          <svg viewBox="0 0 20 20" aria-hidden="true">
            <circle cx="10" cy="10" r="9.5" fill="var(--gold)"/>
            <circle cx="10" cy="10" r="3" fill="none" stroke="var(--white)" stroke-width="1.5"/>
          </svg>
          <span>@vessolinhairstudio</span>
        </li>
      </ul>
    </div>

    <div class="web-pill">www.<strong>vessolinhairstudio</strong>.example</div>
  </section>

</body>
</html>
```